For Sale Sign for Real Estate Agency

We need a For Sale Sign designed for our agency. I want a very simple/elegant sign that says "For Sale" towards the top of the sign (not in huge letters). Most of the sign should be a design/picture with our name and phone number somewhere at the bottom.

One significant detail, it's important that our logo not be too big or the center piece of the sign. Since our company name has the word "rent" in it, people assume the house is for rent, instead of for sale.

I attached our logo and a rough outline of the format I'm looking for.

Again, I'm looking for elegant and simple! Thanks for your time

Industry/Entity Type

Real Estate

Colors

Designer to choose colors to be used in the design.

Requirements
Must have
Nice to have
Should not have
• Nothing tacky!
• Our logo/company name should not be too big or the center piece of the sign. Since our company name has the word "rent" in it, people assume the house is for rent, instead of for sale.

```html
<!DOCTYPE html>
<html lang="en">
<head>
<meta charset="utf-8">
<title>Harborline Realty — For Sale Signs</title>
<link href="https://fonts.googleapis.com/css2?family=Libre+Baskerville:ital,wght@0,400;0,700;1,400&family=Playfair+Display:ital,wght@1,500&display=swap" rel="stylesheet">
<style>
  :root {
    --stage: #e4e4e4;
    --sky-top: #4b55d6;
    --sky-mid: #7a6ad8;
    --dusk: #c98a8a;
    --city: #3d3a2c;
    --red: #d4261f;
    --band: #1e1a1a;
    --gold: #f4c95a;
    --white: #ffffff;
  }
  * { box-sizing: border-box; margin: 0; padding: 0; }
  html, body { width: 837px; height: 1200px; overflow: hidden; }
  body {
    position: relative;
    background: var(--stage);
    font-family: "Libre Baskerville", Georgia, serif;
    color: var(--white);
  }
  .sign { position: absolute; overflow: hidden; background: var(--red); }
  .sign--landscape { left: 122px; top: 58px; width: 596px; height: 418px; }
  .sign--portrait { left: 184px; top: 516px; width: 470px; height: 654px; }
  .sign__art { position: absolute; inset: 0; width: 100%; height: 100%; }

  .headline { position: absolute; left: 0; right: 0; text-align: center; line-height: 1; font-weight: 400; }
  .headline__for { font-family: "Playfair Display", Georgia, serif; font-style: italic; font-weight: 500; color: var(--gold); }
  .headline__sale { font-family: "Libre Baskerville", Georgia, serif; font-weight: 400; color: var(--white); }

  .sign--landscape .headline { top: 24px; left: 168px; right: auto; text-align: left; white-space: nowrap; }
  .sign--landscape .headline__for { font-size: 44px; margin-right: 10px; }
  .sign--landscape .headline__sale { font-size: 62px; }

  .sign--portrait .headline { top: 14px; }
  .sign--portrait .headline__for { display: block; font-size: 62px; }
  .sign--portrait .headline__sale { display: block; font-size: 84px; margin-top: 4px; }

  .call-box {
    position: absolute;
    border: 1px solid rgba(255,255,255,0.6);
    border-radius: 8px;
    text-align: center;
  }
  .call-box__icon { position: absolute; left: 50%; transform: translateX(-50%); }
  .call-box__phone { display: block; font-weight: 400; white-space: nowrap; }
  .call-box__web { display: block; font-style: italic; white-space: nowrap; }

  .sign--landscape .call-box { left: 195px; top: 320px; width: 205px; height: 59px; }
  .sign--landscape .call-box__icon { top: -12px; }
  .sign--landscape .call-box__phone { font-size: 26px; margin-top: 10px; }
  .sign--landscape .call-box__web { font-size: 7.5px; margin-top: 5px; letter-spacing: 2.6px; }

  .sign--portrait .call-box { left: 118px; top: 502px; width: 237px; height: 67px; }
  .sign--portrait .call-box__icon { top: -12px; }
  .sign--portrait .call-box__phone { font-size: 29px; margin-top: 12px; }
  .sign--portrait .call-box__web { font-size: 8.5px; margin-top: 6px; letter-spacing: 3px; }

  .brand { position: absolute; font-weight: 400; color: var(--white); white-space: nowrap; }
  .sign--landscape .brand { left: 16px; top: 372px; font-size: 16px; }
  .sign--portrait .brand { left: 21px; top: 606px; font-size: 18px; }

  .contact { position: absolute; list-style: none; font-size: 9px; line-height: 1.25; }
  .contact li { position: relative; padding-left: 18px; margin-bottom: 4px; }
  .contact svg { position: absolute; left: 2px; top: 1px; }
  .sign--landscape .contact { left: 424px; top: 372px; }
  .sign--portrait .contact { left: 288px; top: 594px; font-size: 9.5px; }
</style>
</head>
<body>

<section class="sign sign--landscape">
  <svg class="sign__art" viewBox="0 0 596 418" preserveAspectRatio="none">
    <defs>
      <linearGradient id="skyL" x1="0" y1="0" x2="0" y2="1">
        <stop offset="0" stop-color="var(--sky-top)"/>
        <stop offset="0.35" stop-color="var(--sky-mid)"/>
        <stop offset="0.5" stop-color="var(--dusk)"/>
        <stop offset="0.8" stop-color="var(--city)"/>
      </linearGradient>
    </defs>
    <rect role="img" aria-label="Evening photograph of a city skyline with towers, a river walk and trees" width="596" height="320" fill="url(#skyL)"/>
    <path d="M0 270 C150 262 300 262 380 290 C450 312 520 300 596 296 L596 418 L0 418 Z" fill="var(--red)"/>
    <path d="M230 264 C320 268 380 300 460 300 C520 300 560 292 596 290 L596 316 C540 318 480 320 430 314 C350 304 300 272 230 264 Z" fill="var(--band)"/>
    <path d="M0 270 C160 258 320 262 430 300" fill="none" stroke="var(--white)" stroke-width="1.2"/>
    <path d="M0 336 C160 330 300 270 420 262 C500 256 560 268 596 276" fill="none" stroke="var(--white)" stroke-width="1.2"/>
    <path d="M120 282 C260 290 420 340 596 340" fill="none" stroke="var(--white)" stroke-width="1.2"/>
  </svg>

  <h1 class="headline"><span class="headline__for">For</span><span class="headline__sale">SALE</span></h1>

  <div class="call-box">
    <svg class="call-box__icon" width="20" height="20" viewBox="0 0 20 20" aria-hidden="true">
      <circle cx="10" cy="10" r="9" fill="var(--red)" stroke="var(--white)" stroke-width="1.5"/>
      <path d="M6.5 5.5 L8.5 5.5 L9.3 8 L8 9 C8.6 10.4 9.6 11.4 11 12 L12 10.7 L14.5 11.5 L14.5 13.5 C10 14 6 10 6.5 5.5 Z" fill="var(--white)"/>
    </svg>
    <span class="call-box__phone">(860) 555-0148</span>
    <span class="call-box__web">www.harborlinerealty.com</span>
  </div>

  <p class="brand">Harborline Realty</p>

  <ul class="contact">
    <li><svg width="10" height="8" viewBox="0 0 10 8" aria-hidden="true"><rect width="10" height="8" fill="var(--white)"/><path d="M0 0 L5 4.5 L10 0" fill="none" stroke="var(--red)" stroke-width="1"/></svg>hello@harborlinerealty.com</li>
    <li><svg width="8" height="11" viewBox="0 0 8 11" aria-hidden="true"><path d="M4 11 C1 7 0 5.5 0 4 A4 4 0 0 1 8 4 C8 5.5 7 7 4 11 Z" fill="var(--white)"/><circle cx="4" cy="4" r="1.5" fill="var(--red)"/></svg>52 Quarry Lane Westbrook,<br>CT 06498</li>
  </ul>
</section>

<section class="sign sign--portrait">
  <svg class="sign__art" viewBox="0 0 470 654" preserveAspectRatio="none">
    <defs>
      <linearGradient id="skyP" x1="0" y1="0" x2="0" y2="1">
        <stop offset="0" stop-color="var(--sky-top)"/>
        <stop offset="0.4" stop-color="var(--sky-mid)"/>
        <stop offset="0.55" stop-color="var(--dusk)"/>
        <stop offset="0.8" stop-color="var(--city)"/>
      </linearGradient>
    </defs>
    <rect role="img" aria-label="Evening photograph of a city skyline with towers, a river walk and trees" width="470" height="480" fill="url(#skyP)"/>
    <path d="M0 440 C120 428 240 428 310 448 C370 464 430 462 470 460 L470 654 L0 654 Z" fill="var(--red)"/>
    <path d="M180 428 C260 432 310 456 370 462 C410 466 445 462 470 460 L470 480 C420 482 370 478 330 468 C270 454 230 436 180 428 Z" fill="var(--band)"/>
    <path d="M0 440 C130 426 260 428 350 466" fill="none" stroke="var(--white)" stroke-width="1.3"/>
    <path d="M0 486 C130 480 240 430 330 426 C400 422 450 432 470 438" fill="none" stroke="var(--white)" stroke-width="1.3"/>
    <path d="M90 448 C200 456 330 486 470 486" fill="none" stroke="var(--white)" stroke-width="1.3"/>
  </svg>

  <h2 class="headline"><span class="headline__for">For</span><span class="headline__sale">SALE</span></h2>

  <div class="call-box">
    <svg class="call-box__icon" width="22" height="22" viewBox="0 0 20 20" aria-hidden="true">
      <circle cx="10" cy="10" r="9" fill="var(--red)" stroke="var(--white)" stroke-width="1.5"/>
      <path d="M6.5 5.5 L8.5 5.5 L9.3 8 L8 9 C8.6 10.4 9.6 11.4 11 12 L12 10.7 L14.5 11.5 L14.5 13.5 C10 14 6 10 6.5 5.5 Z" fill="var(--white)"/>
    </svg>
    <span class="call-box__phone">(860) 555-0148</span>
    <span class="call-box__web">www.harborlinerealty.com</span>
  </div>

  <p class="brand">Harborline Realty</p>

  <ul class="contact">
    <li><svg width="10" height="8" viewBox="0 0 10 8" aria-hidden="true"><rect width="10" height="8" fill="var(--white)"/><path d="M0 0 L5 4.5 L10 0" fill="none" stroke="var(--red)" stroke-width="1"/></svg>hello@harborlinerealty.com</li>
    <li><svg width="8" height="11" viewBox="0 0 8 11" aria-hidden="true"><path d="M4 11 C1 7 0 5.5 0 4 A4 4 0 0 1 8 4 C8 5.5 7 7 4 11 Z" fill="var(--white)"/><circle cx="4" cy="4" r="1.5" fill="var(--red)"/></svg>52 Quarry Lane Westbrook,<br>CT 06498</li>
  </ul>
</section>

</body>
</html>
```